New Business Card Design Project

Use the flyer uploaded and website www.brightoakbuilders.com for inspiration.
List Our Services on Backside of business cards
Marcus Delling
Harborline Builders Inc.
Licensed General Contractors
858-471-6093

Contact Information for Business Card

Use the flyer uploaded and website www.brightoakbuilders.com for inspiration. List Our Services on Backside of business cards Marcus Delling Harborline Builders Inc. Licensed General Contractors 858-471-6093

```html
<!DOCTYPE html>
<html lang="en">
<head>
<meta charset="utf-8">
<title>Harborline Builders – Business Card</title>
<link href="https://fonts.googleapis.com/css2?family=Montserrat:wght@400;500;700&display=swap" rel="stylesheet">
<style>
  :root{
    --stage:#3c3c3c;
    --card:#1b1b1b;
    --ink:#f2f2f2;
    --ink-soft:#cfcfcf;
    --rule:#bdbdbd;
  }
  *{margin:0;padding:0;box-sizing:border-box}
  html,body{width:1200px;height:900px;overflow:hidden}
  body{
    background:var(--stage);
    font-family:'Montserrat',sans-serif;
    color:var(--ink);
    display:flex;flex-direction:column;align-items:center;justify-content:center;gap:40px;
  }
  .card{
    position:relative;width:600px;height:343px;
    background:var(--card);border-radius:22px;
    box-shadow:0 14px 30px rgba(0,0,0,.45);
    overflow:hidden;
  }
  .brand-name{
    font-weight:400;letter-spacing:.1em;text-transform:uppercase;color:var(--ink);white-space:nowrap;
  }
  /* back */
  .card-back .brand-block{
    position:absolute;left:24px;top:0;bottom:0;width:316px;
    display:flex;align-items:center;justify-content:center;gap:10px;
  }
  .card-back .brand-name{font-size:17px}
  .brand-mark{width:11px;height:11px;border:1.5px solid var(--ink);flex:none}
  .divider{position:absolute;left:355px;top:62px;bottom:62px;width:1px;background:var(--rule)}
  .services{position:absolute;left:378px;top:72px}
  .services h2{font-size:17px;font-weight:700;margin-bottom:8px}
  .services ul{list-style:none}
  .services li{font-size:12.5px;line-height:19px;color:var(--ink-soft);padding-left:12px;position:relative}
  .services li::before{content:"";position:absolute;left:0;top:8px;width:4px;height:4px;border-radius:50%;background:var(--ink)}
  /* front */
  .card-front .brand-name{position:absolute;left:48px;top:112px;font-size:20px}
  .person{position:absolute;right:56px;top:40px;text-align:right}
  .person h1{font-size:22px;font-weight:700;line-height:28px}
  .person p{font-size:12.5px;color:var(--ink-soft);margin-top:2px}
  .edge-tab{position:absolute;right:0;top:40px;width:16px;height:34px;background:var(--ink)}
  .address{position:absolute;left:48px;top:196px;font-size:13.5px;line-height:19px;color:var(--ink-soft)}
  .contacts{position:absolute;left:48px;bottom:30px;list-style:none}
  .contacts li{display:flex;align-items:center;gap:14px;font-size:13.5px;line-height:26px;color:var(--ink-soft)}
  .contacts svg{width:14px;height:14px;flex:none}
</style>
</head>
<body>

<section class="card card-back">
  <div class="brand-block">
    <span class="brand-mark"></span>
    <span class="brand-name">Harborline Builders</span>
  </div>
  <div class="divider"></div>
  <div class="services">
    <h2>Our Services</h2>
    <ul>
      <li>Remodel: Kitchen &amp; Bath</li>
      <li>Painting: Interior &amp; Exterior</li>
      <li>Flooring: Carpet, Vinyl, Wood</li>
      <li>Window &amp; Door Replacement</li>
      <li>Plumbing: Repair &amp; Upgrades</li>
      <li>Energy Efficient Upgrades</li>
      <li>Deck &amp; Patio construction</li>
      <li>Water &amp; Mold Damage</li>
      <li>Garage Renovation</li>
    </ul>
  </div>
</section>

<section class="card card-front">
  <div class="edge-tab"></div>
  <div class="person">
    <h1>Marcus Delling</h1>
    <p>Licensed General Contractors</p>
  </div>
  <span class="brand-name">Harborline Builders</span>
  <p class="address">48 Ridgeview Lane, suite 210<br>Alder PA 19034</p>
  <ul class="contacts">
    <li>
      <svg viewBox="0 0 16 16" aria-hidden="true"><path fill="#f2f2f2" d="M3 1.5h3l1.2 3.2-1.8 1.2a9 9 0 0 0 4.7 4.7l1.2-1.8 3.2 1.2v3c0 .8-.7 1.5-1.5 1.5C6.6 14.5 1.5 9.4 1.5 3c0-.8.7-1.5 1.5-1.5z"/></svg>
      858-471-6093
    </li>
    <li>
      <svg viewBox="0 0 16 16" aria-hidden="true"><rect x="1.5" y="3.5" width="13" height="9" fill="#f2f2f2"/><path d="M1.5 3.5 8 9l6.5-5.5" fill="none" stroke="#1b1b1b" stroke-width="1.2"/></svg>
      info@brightoakbuilders.com
    </li>
    <li>
      <svg viewBox="0 0 16 16" aria-hidden="true"><circle cx="8" cy="8" r="6.5" fill="none" stroke="#f2f2f2" stroke-width="1.3"/><ellipse cx="8" cy="8" rx="2.8" ry="6.5" fill="none" stroke="#f2f2f2" stroke-width="1.1"/><path d="M1.5 8h13" stroke="#f2f2f2" stroke-width="1.1"/></svg>
      www.brightoakbuilders.com
    </li>
  </ul>
</section>

</body>
</html>
```